Dermal Care Nursing Circle - Rack Card Design

This is a 2-sided rack card that should be 3.5 inches wide by 8.5 inches tall.

Text (with instructions), logo and website image are attached. For the main image on the front, you can use the attached image, or pull whatever you like off of pictovault.example, and we will purchase the photo from the winning design

The front should have text plus a nurse image, the back should have mostly text with the website image and legend.
Updates

We have received many high quality designs, but it is apparent to us that at the print size we are currently using (3.5x8.5), that the image of the homepage on the back is too small, and not legible. As such, we have decided that we would like to go with a horizontal version at 8.5 wide by 5.5 tall, with a larger more legible version of the website on the back and call outs to one side or the other, please resubmit your designs in that format. Thank you, and sorry for the inconvenience. Ned

Industry/Entity Type

Nurse

Font styles to use
Sans Serif

Colors
876aae
6b449b
b7a5cd
e4daeb

Requirements
Must have
• Please use the color palate from the attached logo, and a nursing image on the front.

```html
<!DOCTYPE html>
<html lang="en">
<head>
<meta charset="utf-8">
<title>Dermal Care Nursing Circle – Rack Card</title>
<link href="https://fonts.googleapis.com/css2?family=Roboto+Condensed:wght@300;400;700&family=Lato:wght@400;700&display=swap" rel="stylesheet">
<style>
  :root{
    --purple:#6b449b;
    --purple-mid:#876aae;
    --purple-light:#b7a5cd;
    --lavender:#e4daeb;
    --violet-glow:#9a66d8;
    --ink:#2b2b2b;
    --footer:#222;
    --scrub:#2e9ad8;
    --scrub-deep:#243f86;
    --page:#ececec;
  }
  *{margin:0;padding:0;box-sizing:border-box}
  html,body{width:1200px;height:1200px;overflow:hidden;background:var(--page)}
  .card{position:absolute;background:#fff;overflow:hidden;box-shadow:0 2px 6px rgba(0,0,0,.18)}
  .card--front{left:90px;top:63px;width:467px;height:1091px}
  .card--back{left:633px;top:63px;width:468px;height:1083px}

  .photo{position:absolute;left:0;width:100%;z-index:0}
  .front-photo{top:290px;height:500px;background:linear-gradient(160deg,#dfe6ea 0%,var(--scrub) 45%,#1d6fb0 100%)}
  .front-shapes,.back-shapes{position:absolute;inset:0;width:100%;height:100%;z-index:1}

  .headline,.brand,.site-bar,.intro,.benefits{z-index:2}

  .headline{position:absolute;left:52px;top:34px;color:#fff;font-family:"Roboto Condensed",sans-serif;line-height:1}
  .headline__lead{font-weight:700;font-size:45px;letter-spacing:-.3px}
  .headline__sub{font-weight:700;font-size:30px;margin-top:2px;letter-spacing:-.2px}
  .headline__thin{font-weight:300;font-size:98px;letter-spacing:-4px;margin-top:2px;margin-left:-4px}
  .headline__bold{font-weight:700;font-size:80px;letter-spacing:-1px;margin-top:2px;margin-left:-2px}

  .brand{position:absolute;top:830px;left:0;width:100%;display:flex;align-items:center;justify-content:center;gap:30px;font-family:"Lato",sans-serif;font-weight:700;color:var(--purple)}
  .brand__foundation{display:flex;align-items:center;gap:10px;font-size:26px;line-height:1.05}
  .brand__dot{width:18px;height:18px;border-radius:50%;background:var(--purple);flex:none}
  .brand__initiative{font-size:30px;line-height:1.1;text-transform:uppercase}

  .site-bar{position:absolute;left:0;bottom:0;width:100%;height:55px;background:var(--footer);color:#fff;font-family:"Lato",sans-serif;font-size:21px;letter-spacing:3.2px;display:flex;align-items:center;justify-content:center}

  .intro{position:absolute;left:31px;top:28px;width:410px;font-family:"Roboto Condensed",sans-serif;font-size:17.5px;line-height:21.5px;color:var(--purple)}
  .intro strong{font-weight:700}
  .benefits{position:absolute;left:30px;top:127px;width:410px;list-style:none;font-family:"Lato",sans-serif;font-size:16.5px;line-height:21px;color:var(--ink)}
  .benefits li{position:relative;padding-left:32px;margin-bottom:20px}
  .benefits li::before{content:"";position:absolute;left:7px;top:9px;width:6px;height:6px;border-radius:50%;background:var(--purple)}
  .back-photo{top:560px;height:523px;background:linear-gradient(170deg,#c79a6a 0%,#a7865f 30%,var(--scrub-deep) 62%,#1f3470 100%)}
</style>
</head>
<body>

<section class="card card--front" aria-label="Front of rack card">
  <div class="photo front-photo" role="img" aria-label="Photo of two smiling nurses in blue scrubs with stethoscopes, one holding a clipboard"></div>
  <svg class="front-shapes" viewBox="0 0 467 1091" preserveAspectRatio="none" aria-hidden="true">
    <defs>
      <linearGradient id="frontViolet" x1="0" y1="0" x2="1" y2="0">
        <stop offset="0" stop-color="#7a4fb8"/>
        <stop offset=".55" stop-color="#9a66d8"/>
        <stop offset="1" stop-color="#6e44a6"/>
      </linearGradient>
    </defs>
    <path d="M0 0H467V346C380 395 250 440 120 445C70 447 30 443 0 436Z" fill="url(#frontViolet)"/>
    <path d="M0 722C140 705 300 740 467 785V800C300 760 140 730 0 742Z" fill="#6b449b"/>
    <path d="M0 738C140 728 300 755 467 795V805C300 770 140 744 0 750Z" fill="#222"/>
    <path d="M0 748C140 738 300 765 467 803V1091H0Z" fill="#fff"/>
  </svg>
  <div class="headline">
    <div class="headline__lead">Inspired By Patients</div>
    <div class="headline__sub">Empowered By Knowledge</div>
    <div class="headline__thin">IMPACTING</div>
    <div class="headline__bold">MELANOMA</div>
  </div>
  <div class="brand">
    <div class="brand__foundation"><span class="brand__dot"></span><span>Skinward<br>Foundation</span></div>
    <div class="brand__initiative">Dermal Care<br>Nursing<br>Circle</div>
  </div>
  <div class="site-bar">www.DermalCareCircle.example</div>
</section>

<section class="card card--back" aria-label="Back of rack card">
  <div class="photo back-photo" role="img" aria-label="Photo of three smiling nurses in navy scrubs standing with arms crossed outside a clinic"></div>
  <svg class="back-shapes" viewBox="0 0 468 1083" preserveAspectRatio="none" aria-hidden="true">
    <path d="M0 0H468V566C330 575 210 605 120 648C80 664 40 670 0 668Z" fill="#fff"/>
    <path d="M160 605C250 575 350 562 468 558V568C350 570 250 582 160 605Z" fill="#222"/>
    <path d="M95 650C200 600 330 578 468 570V586C330 592 210 612 95 650Z" fill="#6b449b"/>
  </svg>
  <p class="intro">You wear many hats and take care of patients with many different tumor types. Check out <strong>DermalCareCircle.example</strong> for free access to:</p>
  <ul class="benefits">
    <li>Hot off the press! Articles from the Journal of Dermal Care Practice outlining practical strategies to manage side-effects and promote adherence to melanoma therapies</li>
    <li>Visual and text-based therapeutic side effect management tools</li>
    <li>A Nurse’s Toolkit with extensive melanoma nursing care resources</li>
    <li>Printable patient resources to provide patients, organized by therapy</li>
    <li>An oncology nurse community forum to share successes, challenges, insights, and solutions</li>
    <li>Online educational modules, newsfeeds, and other material to keep you up to date</li>
    <li>And much more!</li>
  </ul>
</section>

</body>
</html>
```